Alterations to existing business card

Here is my current logo and I want the "cafe and bar" taken off with just the words Lumo and our slogan "Savour the moment" on the card, Plus the logo.
Our Current Business Card is currently 5.5cm by 5.5cm and would like it to remain like this thanks.
The loyalty card can be 10 squares with the logo specifying the 10th coffee free. I would like the cheapest option please.
Also on our business card would like the Facebook logo and instagram Logo with TAZALUMO27 as link to our photos on instagram.

Keep Colour schemes the same please.

On the business cards

Dale Brinton Director
0427916038
dale27lumo@mailvista.test

Paula Ferrisi Principal
0428571963
paulumo@mailvista.test

Thanks Dale

Industry/Entity Type

Business

```html
<!DOCTYPE html>
<html lang="en">
<head>
<meta charset="utf-8">
<title>Lumo Business Card</title>
<link rel="stylesheet" href="https://fonts.googleapis.com/css2?family=Questrial&family=Roboto:wght@400&display=swap">
<style>
  :root {
    --stage: #b0b0b0;
    --card-dark: #232323;
    --card-light: #f7f7f5;
    --gold: #d9a82a;
    --gold-soft: #e8bf45;
    --ink: #1b1b1b;
    --white: #ffffff;
    --ghost: rgba(0, 0, 0, 0.035);
  }
  html, body {
    margin: 0;
    padding: 0;
    width: 1200px;
    height: 698px;
    overflow: hidden;
    background: var(--stage);
  }
  .stage {
    position: relative;
    width: 1200px;
    height: 698px;
    font-family: "Roboto", Arial, sans-serif;
  }
  .card {
    position: absolute;
    width: 334px;
    height: 334px;
    transform: translate(-50%, -50%) rotate(45deg);
  }
  .card--front { left: 355px; top: 344px; background: var(--card-dark); }
  .card--back  { left: 846px; top: 344px; background: var(--card-light); }

  /* Front */
  .brand-ring {
    position: absolute;
    left: 291px;
    top: 242px;
    width: 128px;
    height: 128px;
    border: 3px solid var(--gold);
    border-radius: 50%;
    box-sizing: border-box;
  }
  .brand-name {
    position: absolute;
    left: 255px;
    top: 372px;
    width: 200px;
    margin: 0;
    text-align: center;
    font-family: "Questrial", "Century Gothic", sans-serif;
    font-weight: 400;
    font-size: 52px;
    line-height: 1;
    letter-spacing: 1px;
    color: var(--white);
  }
  .brand-slogan {
    position: absolute;
    left: 255px;
    top: 423px;
    width: 200px;
    margin: 0;
    text-align: center;
    font-family: "Questrial", "Century Gothic", sans-serif;
    font-style: italic;
    font-size: 12px;
    line-height: 14px;
    letter-spacing: 1.4px;
    color: var(--gold-soft);
    text-transform: uppercase;
  }

  /* Back */
  .ghost-ring {
    position: absolute;
    left: 722px;
    top: 220px;
    width: 248px;
    height: 248px;
    border: 8px solid var(--ghost);
    border-radius: 50%;
    box-sizing: border-box;
  }
  .name-frame {
    position: absolute;
    left: 748px;
    top: 277px;
    width: 197px;
    height: 46px;
    border: 1px solid var(--gold);
    box-sizing: border-box;
  }
  .person-name {
    position: absolute;
    left: 748px;
    top: 286px;
    width: 197px;
    margin: 0;
    text-align: center;
    font-family: "Questrial", "Century Gothic", sans-serif;
    font-weight: 400;
    font-size: 22px;
    line-height: 24px;
    color: var(--ink);
  }
  .person-role {
    position: absolute;
    left: 810px;
    top: 315px;
    width: 73px;
    margin: 0;
    text-align: center;
    font-size: 13.5px;
    line-height: 17px;
    color: var(--ink);
    background: var(--card-light);
  }
  .contact {
    position: absolute;
    left: 746px;
    top: 353px;
    width: 200px;
    margin: 0;
    text-align: center;
    font-size: 14px;
    line-height: 17px;
    color: var(--ink);
  }
  .social {
    position: absolute;
    left: 746px;
    top: 400px;
    width: 200px;
    display: flex;
    justify-content: center;
    align-items: center;
    gap: 4px;
    font-size: 13px;
    line-height: 17px;
    color: var(--ink);
  }
  .social-label { margin-right: 3px; }
  .social-mark {
    width: 15px;
    height: 15px;
    background: var(--ink);
    border-radius: 2px;
  }
</style>
</head>
<body>
  <main class="stage">
    <div class="card card--front" aria-hidden="true"></div>
    <div class="card card--back" aria-hidden="true"></div>

    <section class="front-face" aria-label="Card front">
      <div class="brand-ring" aria-hidden="true"></div>
      <h1 class="brand-name">LUMO</h1>
      <p class="brand-slogan">Savour the moment</p>
    </section>

    <section class="back-face" aria-label="Card back">
      <div class="ghost-ring" aria-hidden="true"></div>
      <div class="name-frame" aria-hidden="true"></div>
      <h2 class="person-name">Paula Ferrisi</h2>
      <p class="person-role">Principal</p>
      <p class="contact">0428571963<br>paulumo@mailvista.test</p>
      <div class="social">
        <span class="social-label">Follows On</span>
        <span class="social-mark" role="img" aria-label="Social network link"></span>
        <span class="social-mark" role="img" aria-label="Photo sharing link"></span>
      </div>
    </section>
  </main>
</body>
</html>
```